Corvane Capital Business Cards

These are professional business cards that are for my family office.
Put fake emails and phone numbers as of now until I finalize those components. This family office controls my families investments, assets, and future. The cards should be professional.
..
.
.
.
I just uploaded another variation of a logo I would like to see as a business card to I am inbeteen which logo to use

Target Market(s)

business

Industry/Entity Type

business

Contact Information for Business Card

Professional, wealth related, finance related.

Requirements
Must have
• Logo

```html
<!DOCTYPE html>
<html lang="en">
<head>
<meta charset="utf-8">
<title>Corvane Capital Business Cards</title>
<link href="https://fonts.googleapis.com/css2?family=Montserrat:wght@400;700&display=swap" rel="stylesheet">
<style>
  :root {
    --navy: #1a1f2c;
    --white: #ffffff;
    --grey: #a8a8a8;
    --ink: #1a1f2c;
    --stage: #e9e7e3;
  }
  * { box-sizing: border-box; margin: 0; padding: 0; }
  html, body { width: 1200px; height: 931px; overflow: hidden; }
  body {
    background: var(--stage);
    font-family: "Montserrat", Arial, sans-serif;
    position: relative;
  }
  .card {
    position: absolute;
    left: 320px;
    width: 560px;
    height: 320px;
    border-radius: 16px;
    overflow: hidden;
    box-shadow: 0 10px 26px rgba(0,0,0,0.18);
  }
  .card--back { top: 120px; background: var(--navy); }
  .card--front { top: 490px; background: var(--white); }

  .brand {
    display: flex;
    align-items: center;
    gap: 12px;
    font-family: "Montserrat", Arial, sans-serif;
    font-weight: 700;
    letter-spacing: 0;
    white-space: nowrap;
  }
  .brand__dot { border-radius: 50%; flex: none; }

  .card--back .brand {
    position: absolute;
    left: 0; right: 0; top: 138px;
    justify-content: center;
    color: var(--white);
    font-size: 34px;
  }
  .card--back .brand__dot { width: 22px; height: 22px; border: 2px solid var(--white); }

  .card--front .brand {
    position: absolute;
    right: 36px; top: 54px;
    color: var(--ink);
    font-size: 22px;
  }
  .card--front .brand__dot { width: 16px; height: 16px; border: 2px solid var(--ink); }

  .divider {
    position: absolute;
    left: 36px; right: 36px; top: 150px;
    height: 1.5px;
    background: var(--ink);
  }
  .person {
    position: absolute;
    left: 36px; top: 168px;
    color: var(--ink);
  }
  .person__name { font-weight: 700; font-size: 22px; line-height: 1.1; }
  .person__role { font-size: 12px; margin-top: 2px; }
  .person__rule { width: 170px; height: 1.5px; background: var(--ink); margin: 8px 0; }
  .contact { list-style: none; }
  .contact li {
    display: flex; align-items: center; gap: 10px;
    font-size: 12px; line-height: 21px;
  }
  .contact svg { width: 12px; height: 12px; fill: var(--ink); flex: none; }

  .address {
    position: absolute;
    right: 36px; top: 214px;
    text-align: right;
    font-size: 11px;
    line-height: 1.45;
    color: var(--ink);
  }
  .band { position: absolute; bottom: 0; height: 18px; }
  .band--navy { left: 0; width: 66%; background: var(--navy); clip-path: polygon(0 0, 100% 0, 97.5% 100%, 0 100%); }
  .band--grey { right: 0; width: 35.5%; background: var(--grey); clip-path: polygon(2.5% 0, 100% 0, 100% 100%, 0 100%); }
</style>
</head>
<body>
  <section class="card card--back" aria-label="Card back">
    <div class="brand"><span class="brand__dot"></span>Corvane Capital</div>
  </section>

  <section class="card card--front" aria-label="Card front">
    <div class="brand"><span class="brand__dot"></span>Corvane Capital</div>
    <div class="divider"></div>

    <div class="person">
      <p class="person__name">Marcus Ellery</p>
      <p class="person__role">Owner</p>
      <div class="person__rule"></div>
      <ul class="contact">
        <li><svg viewBox="0 0 24 24" aria-hidden="true"><path d="M6.6 10.8a15.1 15.1 0 0 0 6.6 6.6l2.2-2.2a1 1 0 0 1 1-.25 11.4 11.4 0 0 0 3.6.57 1 1 0 0 1 1 1V20a1 1 0 0 1-1 1A17 17 0 0 1 3 4a1 1 0 0 1 1-1h3.5a1 1 0 0 1 1 1c0 1.25.2 2.45.57 3.57a1 1 0 0 1-.25 1z"/></svg>(555)014-2870</li>
        <li><svg viewBox="0 0 24 24" aria-hidden="true"><path d="M2 5h20v14H2zM2 6l10 7 10-7v2l-10 7L2 8z"/></svg>info@yourdomainname.com</li>
        <li><svg viewBox="0 0 24 24" aria-hidden="true"><path d="M12 2a10 10 0 1 0 0 20 10 10 0 0 0 0-20zm6.9 6h-3a15 15 0 0 0-1.4-3.9A8 8 0 0 1 18.9 8zM12 4c.8 1.2 1.5 2.5 1.9 4h-3.8c.4-1.5 1.1-2.8 1.9-4zM4.3 14a8 8 0 0 1 0-4h3.4a16 16 0 0 0 0 4zm.8 2h3a15 15 0 0 0 1.4 3.9A8 8 0 0 1 5.1 16zm3-8h-3a8 8 0 0 1 4.4-3.9A15 15 0 0 0 8.1 8zM12 20c-.8-1.2-1.5-2.5-1.9-4h3.8c-.4 1.5-1.1 2.8-1.9 4zm2.3-6H9.7a14 14 0 0 1 0-4h4.6a14 14 0 0 1 0 4zm.2 5.9a15 15 0 0 0 1.4-3.9h3a8 8 0 0 1-4.4 3.9zm1.8-5.9a16 16 0 0 0 0-4h3.4a8 8 0 0 1 0 4z"/></svg>www.yourdomainname.com</li>
      </ul>
    </div>

    <p class="address">48 Harbor Point Drive<br>Eastbrook, NJ 07210 USA</p>

    <div class="band band--navy"></div>
    <div class="band band--grey"></div>
  </section>
</body>
</html>
```